Quirky Label Design for an Exciting UK-Based Organic Skincare Company!

We need label designs across our range of products, we are a high quality yet quirky organic skincare company called Simply Cordell, we use frosted glass packaging, and we are just wanting one design done for now, but the winning designer we would want to work with to design the rest of the labels for us. We also want them to design business cards and other literature at some point and maybe even a website page.

Our label design will go on a 63mm tall frosted glass jar which is 62mm in diameter. The actual label dimensions should be, 170 mm (W) x 50 mm (H). The idea is so that it wraps around the whole jar with the design at one side (at the front) and the ingredients on another (at the back).

LABEL 1
Organic Polynesian Whipped Body Butter
Vanilla Bean
120ml

Made with Organic Shea and Cocoa Butters and exotic Monoi de Tahiti

Ingredients (INCI): Organic Raw Shea Butter (Butyrospermum Parkii), Organic Raw Cocoa Butter (Theobroma Cacao), Monoi de Tahiti (Coconut (Cocos nucifera) oil (and) Tiare (Gardenia tahitensis) flower), Organic Sweet Almond Oil (Prunus Amygdalus Dulcis), Organic Madagascan Vanilla Extract (Vanillin)

Handmade by Simply Cordell Ltd
14 Fernwick Lane, Bournemouth BH4 9QT, UK
Batch:

OPTIONAL WRITING (if it fits in):
100% Natural and Organic
Intensely Moisturising

LABEL 2
Mango Smoothie
120ml

Ingredients (INCI): Organic Raw Shea Butter (Butyrospermum Parkii), Organic Raw Cocoa Butter (Theobroma Cacao), Monoi de Tahiti (Coconut (Cocos nucifera) oil (and) Tiare (Gardenia tahitensis) flower), Organic Sweet Almond Oil (Prunus Amygdalus Dulcis), Organic Mango Flavour (Aroma)

Batch:

100% Natural and Organic
Intensely Moisturising

I have attached a picture of the jar we use and the lid we use for these products, as well as our logo. I've also attached a 'Handmade in Dorset' stamp which we'd like to go on there if possible, along with a shelf life symbol.

I am thinking the background colour of the labels will be either white or even brown paper colour. Perhaps it would be interesting to see it in both. UPDATE: We have decided on white background now, not brown.

The final design should denote handmade, organic, high quality, pure, yet quirky and original / unique. I am thinking perhaps a seemingly hand-drawn black leaf outline? Could fit the bill, but as I say, up to you. Something that says handmade yet professional.

I'd like to have the original Photoshop files from the winning designer so we can use them as a template for the rest of our horizontal labels.
Updates

Project Deadline Extended
Reason: Just need a few more days for designs we like to be worked on further, and to review new designs!

Target Market(s)

Everyone that appreciates a good quality skincare product focusing on natural & organic. Price is mid-range to high

Industry/Entity Type

It Company

Requirements
Must have
• Must make the product look high quality & organic yet quirky and accessible. Must have our logo and the shelf life symbol and the writing as above.
Nice to have
• Nice to have the 'handmade' stamp attached, but not absolutely necessary if it doesn't fit within your design.

```html
<!DOCTYPE html>
<html lang="en">
<head>
<meta charset="utf-8">
<title>Simply Cordell – Whipped Body Butter Labels</title>
<link rel="stylesheet" href="https://fonts.googleapis.com/css2?family=Open+Sans:wght@300;400;600;700&family=Pacifico&display=swap">
<style>
  :root {
    --paper: #ffffff;
    --ink: #4a4a4a;
    --ink-soft: #6b6b6b;
    --rule: #c9c9c9;
    --white: #ffffff;
    --vanilla-edge: #ec3a96;
    --mango-edge: #8fd3f0;
    --stamp-vanilla: #f39a3c;
    --stamp-mango: #a34de0;
  }
  * { margin: 0; padding: 0; box-sizing: border-box; }
  html, body { width: 1200px; height: 1200px; overflow: hidden; background: var(--paper); }
  .canvas { position: relative; width: 1200px; height: 1200px; background: var(--paper); font-family: "Open Sans", sans-serif; color: var(--ink); }

  .label { position: absolute; left: 80px; width: 1040px; height: 306px; border: 1.5px solid var(--rule); background: var(--white); overflow: hidden; }
  .label--vanilla { top: 250px; }
  .label--mango { top: 650px; }

  .label__back { position: absolute; left: 0; top: 0; width: 362px; height: 100%; padding: 16px 18px 0 14px; font-size: 12.6px; line-height: 1.42; color: var(--ink-soft); }
  .label__ingredients { text-align: justify; }
  .label__ingredients strong { font-weight: 700; color: var(--ink); }
  .label__maker { margin-top: 34px; }

  .label__front { position: absolute; left: 362px; top: 0; width: 500px; height: 100%; border-left: 4px solid var(--edge); }
  .label--vanilla .label__front { --edge: var(--vanilla-edge); }
  .label--mango .label__front { --edge: var(--mango-edge); }
  .wash { position: absolute; inset: 0; width: 100%; height: 100%; }

  .brand { position: absolute; left: 0; width: 260px; top: 22px; text-align: center; color: var(--white); font-weight: 700; font-size: 34px; line-height: 1.05; text-transform: uppercase; letter-spacing: 1px; }
  .brand__mark { display: inline-block; width: 10px; height: 10px; background: var(--white); border-radius: 50%; vertical-align: middle; margin-right: 6px; }
  .volume { position: absolute; left: 280px; top: 14px; font-size: 24px; font-weight: 400; color: var(--ink); }
  .product { position: absolute; left: 0; width: 260px; top: 128px; text-align: center; color: var(--white); font-weight: 300; text-transform: uppercase; line-height: 1.2; }
  .product__line1 { font-size: 24px; }
  .product__line2 { font-size: 20px; margin-top: 4px; }
  .product__line3 { display: inline-block; font-size: 22px; margin-top: 10px; padding-bottom: 4px; border-bottom: 1.5px solid var(--white); }
  .flavour { position: absolute; left: 0; width: 260px; top: 232px; text-align: center; color: var(--white); font-family: "Pacifico", cursive; font-size: 25px; }
  .stamp { position: absolute; left: 262px; top: 165px; width: 104px; height: 104px; border-radius: 50%; background: var(--white); border: 5px solid var(--stamp); opacity: 0.95; }
  .label--vanilla .stamp { --stamp: var(--stamp-vanilla); }
  .label--mango .stamp { --stamp: var(--stamp-mango); }

  .label__claims { position: absolute; left: 805px; top: 84px; width: 220px; color: var(--ink-soft); font-size: 17.5px; line-height: 1.3; font-weight: 400; }
  .claims__pct { font-size: 37px; font-weight: 600; line-height: 1; margin-bottom: 8px; color: var(--ink-soft); }
  .claims__made { font-family: "Pacifico", cursive; font-size: 17px; margin-top: 28px; margin-bottom: 2px; color: var(--ink); }
  .claims__list { font-size: 16.5px; line-height: 1.25; }
</style>
</head>
<body>
<div class="canvas">

  <section class="label label--vanilla">
    <div class="label__back">
      <p class="label__ingredients"><strong>Ingredients (INCI):</strong> Organic Raw Shea Butter (Butyrospermum Parkii), Organic Raw Cocoa Butter (Theobroma Cacao), Monoi de Tahiti (Coconut (Cocos nucifera) oil (and) Tiare (Gardenia tahitensis) flower), Organic Sweet Almond Oil (Prunus Amygdalus Dulcis), Organic Madagascan Vanilla Extract (Vanillin).</p>
      <p class="label__maker">Handmade<br>by Simply Cordell Ltd<br>14 Fernwick Lane,<br>Bournemouth BH4 9QT, UK<br>Batch:</p>
    </div>
    <div class="label__front">
      <svg class="wash" viewBox="0 0 500 306" preserveAspectRatio="none" role="img" aria-label="Watercolour wash in magenta, red and orange">
        <defs>
          <linearGradient id="washVanilla" x1="0" y1="0" x2="1" y2="0.2">
            <stop offset="0" stop-color="#ea3a98"/>
            <stop offset="0.35" stop-color="#ef4534"/>
            <stop offset="0.6" stop-color="#f7902a"/>
            <stop offset="0.85" stop-color="#fbcf92"/>
            <stop offset="1" stop-color="#fde9cf" stop-opacity="0"/>
          </linearGradient>
        </defs>
        <path d="M0 0 H260 C300 10 320 40 300 70 C360 90 330 150 380 170 C430 200 440 250 500 306 H0 Z" fill="url(#washVanilla)"/>
      </svg>
      <div class="brand"><span class="brand__mark"></span>Simply<br>Cordell</div>
      <div class="volume">120ml</div>
      <div class="product">
        <div class="product__line1">Organic</div>
        <div class="product__line2">Polynesian Whipped</div>
        <div class="product__line3">Body Butter</div>
      </div>
      <div class="flavour">vanilla bean</div>
      <div class="stamp" role="img" aria-label="Handmade stamp"></div>
    </div>
    <div class="label__claims">
      <div class="claims__pct">100%</div>
      <div>Natural and Organic<br>Intensely Moisturising</div>
      <div class="claims__made">made with</div>
      <div class="claims__list">Organic Shea<br>&amp; Cocoa Butters<br>&amp; exotic Monoi de Tahiti</div>
    </div>
  </section>

  <section class="label label--mango">
    <div class="label__back">
      <p class="label__ingredients"><strong>Ingredients (INCI):</strong> Organic Raw Shea Butter (Butyrospermum Parkii), Organic Raw Cocoa Butter (Theobroma Cacao), Monoi de Tahiti (Coconut (Cocos nucifera) oil (and) Tiare (Gardenia tahitensis) flower), Organic Sweet Almond Oil (Prunus Amygdalus Dulcis), Organic Madagascan Vanilla Extract (Vanillin).</p>
      <p class="label__maker">Handmade<br>by Simply Cordell Ltd<br>14 Fernwick Lane,<br>Bournemouth BH4 9QT, UK<br>Batch:</p>
    </div>
    <div class="label__front">
      <svg class="wash" viewBox="0 0 500 306" preserveAspectRatio="none" role="img" aria-label="Watercolour wash in sky blue, violet and lilac">
        <defs>
          <linearGradient id="washMango" x1="0" y1="1" x2="1" y2="0">
            <stop offset="0" stop-color="#3fb3f0"/>
            <stop offset="0.3" stop-color="#4aa8ee"/>
            <stop offset="0.5" stop-color="#9a45e6"/>
            <stop offset="0.75" stop-color="#c986ef"/>
            <stop offset="1" stop-color="#ecd3f7" stop-opacity="0.2"/>
          </linearGradient>
        </defs>
        <path d="M0 0 H300 C340 5 370 30 390 55 C400 90 360 110 380 140 C420 190 400 240 440 306 H0 Z" fill="url(#washMango)"/>
      </svg>
      <div class="brand"><span class="brand__mark"></span>Simply<br>Cordell</div>
      <div class="volume">120ml</div>
      <div class="product">
        <div class="product__line1">Organic</div>
        <div class="product__line2">Polynesian Whipped</div>
        <div class="product__line3">Body Butter</div>
      </div>
      <div class="flavour">mango smoothie</div>
      <div class="stamp" role="img" aria-label="Handmade stamp"></div>
    </div>
    <div class="label__claims">
      <div class="claims__pct">100%</div>
      <div>Natural and Organic<br>Intensely Moisturising</div>
      <div class="claims__made">made with</div>
      <div class="claims__list">Organic Shea<br>&amp; Cocoa Butters<br>&amp; exotic Monoi de Tahiti</div>
    </div>
  </section>

</div>
</body>
</html>
```